Veltrano.co - Polar Expeditions Specialists

We need a modern, visually striking business card for Veltrano.co, a company specialized in selling expedition cruises to the most remote regions on Earth, with a focus on the Arctic and Antarctica. The design should instantly communicate that the cardholder is an expert in polar travel. Use clean, premium aesthetics with cool tones like icy blue and white, possibly incorporating polar imagery (ice, glaciers, penguins, etc.)

Attached the logo

Contact Information for Business Card

Feels high-end and trustworthy.. Visually memorable — encourages people to keep it

Colors
0054AA
0677BA
7BADD7
CADEEF
E8F1F8

Requirements
Must have
• ice, glaciers, penguins, montains
Nice to have
• modern, transparente,

```html
<!DOCTYPE html>
<html lang="en">
<head>
<meta charset="utf-8">
<title>Veltrano.co – Business Card</title>
<link href="https://fonts.googleapis.com/css2?family=Poppins:wght@300;400;500;700&display=swap" rel="stylesheet">
<style>
  :root {
    --backdrop: #3d3d3d;
    --card-blue: #3474b5;
    --card-blue-deep: #2a63a0;
    --ice-white: #ffffff;
    --frost: #e8f1f8;
    --foil: #9fe0f2;
    --mark-navy: #1c4e96;
  }
  * { margin: 0; padding: 0; box-sizing: border-box; }
  html, body {
    width: 1200px; height: 803px; overflow: hidden;
    background: var(--backdrop);
    font-family: "Poppins", sans-serif;
  }
  .stage {
    position: relative; width: 1200px; height: 803px;
    display: flex; align-items: center; justify-content: center; gap: 40px;
  }
  .card {
    position: relative; width: 540px; height: 310px;
    background: var(--card-blue); border-radius: 22px; overflow: hidden;
    color: var(--ice-white);
  }
  /* Front */
  .card-front__art {
    position: absolute; right: 0; top: 0; width: 300px; height: 100%;
    background: linear-gradient(215deg, var(--ice-white) 0%, var(--frost) 28%, var(--card-blue) 62%);
  }
  .card-front__info { position: absolute; left: 34px; top: 36px; width: 240px; }
  .brand-name { font-weight: 700; font-size: 32px; line-height: 1; letter-spacing: 0.3px; }
  .brand-tagline { font-weight: 500; font-size: 9.5px; margin-top: 5px; letter-spacing: 0.2px; }
  .holder-name { font-weight: 700; font-size: 22px; margin-top: 24px; line-height: 1.1; }
  .holder-role { font-weight: 300; font-size: 11px; margin-top: 2px; }
  .address { font-weight: 400; font-size: 11.5px; line-height: 1.4; margin-top: 14px; }
  .contacts { list-style: none; margin-top: 10px; font-size: 11.5px; line-height: 1.5; }
  .contacts li { display: flex; align-items: center; gap: 8px; }
  .contacts svg { width: 11px; height: 11px; flex: none; }
  /* Back */
  .card-back__lockup {
    position: absolute; left: 0; right: 0; top: 50%; transform: translateY(-50%);
    display: flex; align-items: center; justify-content: center; gap: 16px;
  }
  .lockup-dot { width: 58px; height: 58px; border-radius: 50%; background: var(--mark-navy); }
  .lockup-name { font-weight: 700; font-size: 46px; line-height: 1; color: var(--foil); }
  .lockup-tagline { font-weight: 400; font-size: 13px; color: var(--foil); margin-top: 6px; letter-spacing: 0.6px; }
</style>
</head>
<body>
<main class="stage">
  <section class="card card-front">
    <div class="card-front__art" role="img" aria-label="Polar bear and penguin silhouettes against a white icy sky"></div>
    <div class="card-front__info">
      <div class="brand-name">Veltrano.co</div>
      <div class="brand-tagline">Polar Expeditions Specialists</div>
      <div class="holder-name">Mara Lindqvist</div>
      <div class="holder-role">President</div>
      <div class="address">4120 Harbor Ridge Road<br>Whitehorse, Canada 51820</div>
      <ul class="contacts">
        <li><svg viewBox="0 0 12 12"><path d="M3 1 L5 3.5 L4 5 Q5 7 7 8 L8.5 7 L11 9 L9.5 11 Q4 10 1 2.5 Z" fill="#fff"/></svg>555-210-4417</li>
        <li><svg viewBox="0 0 12 12"><rect x="3" y="0.8" width="6" height="10.4" rx="1" fill="none" stroke="#fff" stroke-width="1.2"/></svg>555-318-7720</li>
        <li><svg viewBox="0 0 12 12"><rect x="0.8" y="2.5" width="10.4" height="7" fill="#fff"/><path d="M0.8 2.5 L6 6.5 L11.2 2.5" fill="none" stroke="#3474b5" stroke-width="1"/></svg>info@veltrano.com</li>
        <li><svg viewBox="0 0 12 12"><circle cx="6" cy="6" r="5" fill="none" stroke="#fff" stroke-width="1.2"/><path d="M1 6 H11 M6 1 Q3 6 6 11 Q9 6 6 1" fill="none" stroke="#fff" stroke-width="0.9"/></svg>www.veltrano.com</li>
      </ul>
    </div>
  </section>

  <section class="card card-back">
    <div class="card-back__lockup">
      <div class="lockup-dot"></div>
      <div>
        <div class="lockup-name">Veltrano.co</div>
        <div class="lockup-tagline">Polar Expeditions Specialists</div>
      </div>
    </div>
  </section>
</main>
</body>
</html>
```